Stationary Set Rebrand for Brennick

We are a Canadian Distribution and Service Company that was established in 1969. Over the past 5 decades we have expanded our business and have warehouses across Canada. We specialize in adhesive tapes, adhesives, films, safety, warehouse, shipping, janitorial and packaging supplies.

We have updated our logo design and would like a new corporate branding identity that includes a new fresh Stationary Set (Business Cards, Letterhead, Letterhead MS Word, Envelope, Presentation Folders, Email Signatures, Notepad Covers, etc.)

Target Market(s)

Industrial Business Sector

Font styles to use
Sans Serif

Colors
0054AA
0677BA
7BADD7
CADEEF
E8F1F8
0094D4
00A9DD
6FCCEA
C7EBF8
E9F6FB
00AB8E
00BBA5
67D7C9
C6EFE9
E9F9F6
EB3D1F
EC4F4E
F09395
F8D3D4
FCEDEE

Requirements
Should not have
• Colors not too light, darker colours preferred

```html
<!DOCTYPE html>
<html lang="en">
<head>
<meta charset="utf-8">
<title>Brennick Business Card</title>
<link rel="stylesheet" href="https://fonts.googleapis.com/css2?family=Michroma&family=Rajdhani:wght@500;600;700&display=swap">
<style>
  :root {
    --backdrop: #e3e3e3;
    --card-white: #ffffff;
    --card-dark: #2b2b2b;
    --ink: #1e1e1e;
    --ink-soft: #4a4a4a;
    --muted: #6b6b6b;
    --rule: #b9b9b9;
    --brand-red: #d9232a;
    --watermark: #fcecee;
    --mark-dark: #5c5c5c;
  }
  * { margin: 0; padding: 0; box-sizing: border-box; }
  html, body {
    width: 1200px; height: 1200px; overflow: hidden;
    background: var(--backdrop);
    font-family: "Rajdhani", sans-serif;
  }
  .sheet { position: relative; width: 1200px; height: 1200px; }

  .card { position: absolute; width: 696px; height: 398px; overflow: hidden; }
  .card--front { left: 262px; top: 156px; background: var(--card-white); }
  .card--back { left: 258px; top: 651px; background: var(--card-dark); }

  .watermark-disc {
    position: absolute; left: -90px; top: 20px;
    width: 420px; height: 420px; border-radius: 50%;
    background: var(--watermark);
  }

  .wordmark { position: absolute; display: flex; align-items: center; gap: 10px; }
  .wordmark__name { font-weight: 700; line-height: 1; letter-spacing: 1px; }
  .wordmark__square { width: 16px; height: 16px; background: var(--brand-red); }

  .card--front .wordmark { right: 50px; top: 48px; }
  .card--front .wordmark__name { font-size: 72px; color: var(--ink); }

  .card--back .wordmark { left: 50%; top: 50%; transform: translate(-50%, -50%); }
  .card--back .wordmark__name { font-size: 84px; color: var(--mark-dark); }
  .card--back .wordmark__square { width: 18px; height: 18px; }

  .person { position: absolute; left: 48px; top: 226px; }
  .person__name {
    font-family: "Michroma", sans-serif; font-size: 22px; font-weight: 400;
    color: var(--brand-red); letter-spacing: 0.5px; line-height: 1.1;
    -webkit-text-stroke: 0.8px var(--brand-red);
  }
  .person__title { font-size: 15px; font-weight: 500; color: var(--muted); margin-top: 6px; letter-spacing: 0.5px; }

  .divider { position: absolute; left: 48px; top: 284px; width: 600px; height: 1px; background: var(--rule); }

  .contacts { position: absolute; left: 48px; top: 293px; list-style: none; }
  .contacts li {
    display: flex; align-items: center; gap: 8px;
    font-size: 17px; font-weight: 500; color: var(--ink-soft);
    height: 21px; letter-spacing: 0.5px;
  }
  .contacts svg { width: 14px; height: 14px; flex: none; fill: var(--brand-red); }

  .address {
    position: absolute; right: 42px; top: 295px; text-align: right;
    font-size: 17px; font-weight: 500; color: var(--ink-soft);
    line-height: 22px; letter-spacing: 0.5px; font-style: normal;
  }
</style>
</head>
<body>
<main class="sheet">
  <section class="card card--front">
    <div class="watermark-disc" aria-hidden="true"></div>

    <div class="wordmark">
      <span class="wordmark__name">Brennick</span>
      <span class="wordmark__square" aria-hidden="true"></span>
    </div>

    <div class="person">
      <h1 class="person__name">MARTIN COLE</h1>
      <p class="person__title">President</p>
    </div>

    <div class="divider"></div>

    <ul class="contacts">
      <li>
        <svg viewBox="0 0 16 16" aria-hidden="true"><path d="M3.6 1.2l2.4 2.6-1.3 1.9c.9 2 2.5 3.7 4.6 4.7l1.9-1.3 2.6 2.4-1.6 2.6C6.8 13.8 2.2 9.2 1 3z"/></svg>
        604-555-0182
      </li>
      <li>
        <svg viewBox="0 0 16 16" aria-hidden="true"><path d="M4 0h8a1 1 0 0 1 1 1v14a1 1 0 0 1-1 1H4a1 1 0 0 1-1-1V1a1 1 0 0 1 1-1zm.8 1.6v10.6h6.4V1.6zM8 13a.9.9 0 1 0 0 1.8A.9.9 0 0 0 8 13z"/></svg>
        604-555-0147
      </li>
      <li>
        <svg viewBox="0 0 16 16" aria-hidden="true"><path d="M1 3.5h14v9H1zm1.4 1.2v.3L8 9l5.6-4v-.3zm0 1.8v4.8h11.2V6.5L8 10.5z"/></svg>
        info@brennick.com
      </li>
    </ul>

    <address class="address">
      412 Harbourview Road<br>
      Kamloops, Canada V2C 4K8<br>
      www.brennick.com
    </address>
  </section>

  <section class="card card--back">
    <div class="wordmark">
      <span class="wordmark__name">Brennick</span>
      <span class="wordmark__square" aria-hidden="true"></span>
    </div>
  </section>
</main>
</body>
</html>
```